Quill Physical Therapy Website

I would need a clean modern website built to showcase my Physical therapy brand and services. I would need a simple but descriptive website that can ultimately connect my patients to my electronic medical portal so they may book an appointment..

```html
<!DOCTYPE html>
<html lang="en">
<head>
<meta charset="utf-8">
<title>Quill Physical Therapy</title>
<link rel="stylesheet" href="https://fonts.googleapis.com/css2?family=Montserrat:ital,wght@0,400;0,500;0,600;0,700;0,800;1,400&family=Open+Sans:ital,wght@0,400;0,600;1,400&display=swap">
<style>
:root{
  --teal:#0f7f7a;
  --teal-dark:#0a625e;
  --green:#6cc04a;
  --ink:#1f1f1f;
  --muted:#777;
  --light:#f1f2f2;
  --white:#fff;
}
*{box-sizing:border-box;margin:0;padding:0}
html,body{width:1200px;height:4628px;overflow:hidden}
body{position:relative;background:var(--white);font-family:"Open Sans",sans-serif;color:var(--ink)}
.abs{position:absolute}
.heading{font-family:"Montserrat",sans-serif;font-weight:700;font-size:34px;letter-spacing:1px;text-align:center;color:var(--ink);left:0;width:1200px}
.btn{position:absolute;background:var(--teal);color:#fff;font-family:"Montserrat",sans-serif;font-weight:700;font-size:14px;letter-spacing:.5px;border-radius:24px;display:flex;align-items:center;justify-content:center}

/* top bar */
.topbar{top:0;left:0;width:1200px;height:50px;background:var(--teal);color:#fff;font-family:"Montserrat",sans-serif;font-size:13px;font-weight:600}
.topbar .mail{position:absolute;left:112px;top:16px;display:flex;gap:8px;align-items:center}
.topbar .call{position:absolute;right:112px;top:16px;display:flex;gap:8px;align-items:center}
.nav{top:50px;left:0;width:1200px;height:86px;background:#fff}
.nav a{position:absolute;top:38px;font-family:"Montserrat",sans-serif;font-size:13px;font-weight:600;color:var(--ink);text-decoration:none}
.nav a.active{color:var(--green)}
.brand-name{position:absolute;left:520px;top:22px;width:260px;text-align:center;font-family:"Montserrat",sans-serif;font-weight:700;font-size:21px;line-height:24px;color:var(--teal);letter-spacing:.5px}

/* hero */
.hero{top:136px;left:0;width:1200px;height:750px;background:linear-gradient(110deg,#dfe7ec 0%,#b9c9d4 30%,#8aa0b2 55%,#d7dde0 100%)}
.hero-title{position:absolute;top:434px;left:0;width:1200px;text-align:center;font-family:"Montserrat",sans-serif;font-weight:700;font-size:48px;line-height:52px;color:#fff;text-shadow:0 2px 6px rgba(0,0,0,.35)}
.slider-arrow{position:absolute;width:48px;height:48px;border-radius:50%;background:rgba(40,40,40,.7);display:flex;align-items:center;justify-content:center}

/* why choose */
.feature{position:absolute;top:1078px;width:230px;text-align:center}
.feature .icon{width:126px;height:126px;border-radius:50%;background:var(--teal);margin:0 auto;display:flex;align-items:center;justify-content:center}
.feature .icon.ring{box-shadow:0 0 0 5px var(--green)}
.feature .num{font-family:"Montserrat",sans-serif;font-weight:600;font-size:14px;color:var(--teal);margin-top:14px}
.feature h3{font-family:"Montserrat",sans-serif;font-weight:700;font-size:14px;margin-top:6px}
.feature p{font-size:12px;color:var(--muted);line-height:21px;margin-top:6px}

/* about */
.about{top:1429px;left:0;width:1200px;height:670px;background:linear-gradient(90deg,#eeeff0,#e4e6e7 50%,#f2f3f3)}
.about h2{position:absolute;left:612px;top:84px;font-family:"Montserrat",sans-serif;font-weight:700;font-size:34px}
.about p{position:absolute;left:612px;top:138px;width:470px;font-size:12.5px;line-height:22.5px;color:#555}
.about .call-label{position:absolute;left:612px;top:505px;font-family:"Montserrat",sans-serif;font-weight:700;font-size:13px}
.about .call-num{position:absolute;left:612px;top:525px;font-family:"Montserrat",sans-serif;font-weight:700;font-size:20px}
.about-name{position:absolute;left:150px;top:210px;width:410px;text-align:center;font-family:"Montserrat",sans-serif;font-weight:700;font-size:40px;line-height:50px;color:var(--teal)}

/* services */
.service{position:absolute;top:2275px;width:234px;height:290px}
.service .photo{width:100%;height:100%}
.service span{position:absolute;left:0;width:100%;top:226px;text-align:center;font-family:"Montserrat",sans-serif;font-weight:700;font-size:16px;color:#fff;text-shadow:0 1px 4px rgba(0,0,0,.6)}
.service .go{position:absolute;left:92px;top:262px;width:50px;height:50px;border-radius:50%;background:#fff;box-shadow:0 2px 6px rgba(0,0,0,.2);display:flex;align-items:center;justify-content:center}

/* testimonials */
.testi{top:2688px;left:0;width:1200px;height:740px}
.testi h2{position:absolute;top:116px;left:0;width:1200px;text-align:center;font-family:"Montserrat",sans-serif;font-weight:700;font-size:34px;color:#fff;letter-spacing:1px}
.quote{position:absolute;top:197px;width:474px;height:290px;background:#fff;border-radius:26px;padding:26px 36px 0 90px}
.quote .mark{position:absolute;left:28px;top:26px;font-family:"Montserrat",sans-serif;font-weight:800;font-size:70px;line-height:60px;color:var(--green)}
.quote p{font-family:"Montserrat",sans-serif;font-style:italic;font-size:12px;line-height:22.5px;color:#777}
.quote .avatar{position:absolute;left:26px;top:200px;width:72px;height:72px;border-radius:50%;background:linear-gradient(135deg,#d7c4b8,#8c7568)}
.quote .who{position:absolute;left:110px;top:208px;font-family:"Montserrat",sans-serif;font-weight:700;font-size:20px}
.quote .co{position:absolute;left:110px;top:238px;font-family:"Montserrat",sans-serif;font-size:14px;color:#777;letter-spacing:.5px}
.round{position:absolute;width:46px;height:46px;border-radius:50%;background:#1f3a36;display:flex;align-items:center;justify-content:center}

/* blog */
.post{position:absolute;top:3602px;width:311px;text-align:center}
.post .photo{width:311px;height:204px;position:relative}
.post .date{position:absolute;left:16px;top:14px;width:52px;height:52px;border-radius:50%;background:var(--green);border:3px solid #fff;color:#fff;font-family:"Montserrat",sans-serif;font-weight:700;font-size:11px;line-height:13px;display:flex;flex-direction:column;align-items:center;justify-content:center}
.post h3{font-family:"Montserrat",sans-serif;font-weight:700;font-size:19px;line-height:22px;margin-top:24px}
.post .by{font-family:"Montserrat",sans-serif;font-weight:600;font-size:12px;color:var(--green);margin-top:8px}
.post p{font-size:12px;line-height:20px;color:#666;margin-top:6px;padding:0 26px}
.post .btn{position:relative;margin:20px auto 0;width:162px;height:44px}

/* footer */
.footer{top:4218px;left:0;width:1200px;height:410px}
.fcol{position:absolute;top:144px;color:#fff}
.fcol h4{font-family:"Montserrat",sans-serif;font-weight:700;font-size:14px;margin-bottom:18px}
.fcol li{list-style:none;font-size:12.5px;line-height:27px;display:flex;align-items:center;gap:10px}
.fcol .ic{width:26px;height:26px;border-radius:50%;background:var(--green);display:inline-block}
.fdiv{position:absolute;top:144px;width:1px;height:165px;background:rgba(255,255,255,.25)}
.copy{position:absolute;top:362px;left:0;width:1200px;text-align:center;color:#fff;font-size:12.5px}
</style>
</head>
<body>

<header>
  <div class="abs topbar">
    <div class="mail"><svg width="14" height="12" viewBox="0 0 14 12"><rect x="1" y="1" width="12" height="10" fill="none" stroke="#fff" stroke-width="1.5"/><path d="M1 1l6 5 6-5" fill="none" stroke="#fff" stroke-width="1.5"/></svg>hello@quillphysio.com</div>
    <div class="call"><svg width="13" height="13" viewBox="0 0 24 24"><path fill="#fff" d="M6.6 10.8a15 15 0 006.6 6.6l2.2-2.2a1 1 0 011-.25 11.4 11.4 0 003.6.57 1 1 0 011 1V20a1 1 0 01-1 1A17 17 0 013 4a1 1 0 011-1h3.5a1 1 0 011 1c0 1.25.2 2.45.57 3.6a1 1 0 01-.25 1z"/></svg>Call us : +1 555 014 2290</div>
  </div>
  <nav class="abs nav">
    <a class="active" style="left:110px">HOME</a>
    <a style="left:198px">ABOUT US</a>
    <a style="left:316px">SERVICES</a>
    <a style="left:432px">PATIENTS</a>
    <div class="brand-name">QUILL PHYSICAL<br>THERAPY</div>
    <a style="left:802px">REVIEWS</a>
    <a style="left:912px">BLOG</a>
    <a style="left:996px">CONTACT US</a>
  </nav>
</header>

<section class="abs hero">
  <div role="img" aria-label="Physical therapist guiding an older woman through a floor stretching exercise in a bright clinic" style="position:absolute;inset:0;background:radial-gradient(ellipse at 60% 40%,rgba(255,255,255,.25),transparent 60%)"></div>
  <div class="slider-arrow" style="left:32px;top:312px"><svg width="12" height="12" viewBox="0 0 12 12"><path d="M8 1L3 6l5 5" stroke="#fff" stroke-width="2" fill="none"/></svg></div>
  <div class="slider-arrow" style="left:1120px;top:312px"><svg width="12" height="12" viewBox="0 0 12 12"><path d="M4 1l5 5-5 5" stroke="#fff" stroke-width="2" fill="none"/></svg></div>
  <h1 class="hero-title">QUILL PHYSICAL<br>THERAPY</h1>
  <div class="btn" style="left:519px;top:557px;width:162px;height:40px;font-size:13px">GET STARTED</div>
  <svg class="abs" style="left:0;top:520px" width="1200" height="232" viewBox="0 0 1200 232">
    <path d="M0 130 Q420 300 1200 70 L1200 232 L0 232Z" fill="#fff"/>
    <path d="M0 60 Q300 260 640 225 Q380 230 0 110Z" fill="var(--teal)"/>
    <path d="M0 120 Q400 280 1200 60 L1200 90 Q420 300 0 140Z" fill="var(--teal)"/>
    <path d="M200 205 Q700 250 1200 100 L1200 125 Q720 260 200 205Z" fill="var(--green)"/>
  </svg>
</section>

<section>
  <h2 class="abs heading" style="top:988px">WHY CHOOSE US</h2>
  <div class="feature" style="left:100px"><div class="icon"><svg width="60" height="60" viewBox="0 0 60 60" fill="none" stroke="#fff" stroke-width="2.5"><circle cx="30" cy="14" r="6"/><path d="M14 36h32M18 36v12M42 36v12M22 36l8-14 8 14"/></svg></div><div class="num">01</div><h3>LOREM IPSUM DOLOR</h3><p>Duis aute irure dolor in repreh enderit in voluptate velit esse cillum</p></div>
  <div class="feature" style="left:357px"><div class="icon"><svg width="60" height="60" viewBox="0 0 60 60" fill="none" stroke="#fff" stroke-width="2.5"><circle cx="24" cy="16" r="6"/><path d="M12 44h36M16 44l8-20 14 8M38 32l6 12"/></svg></div><div class="num">02</div><h3>LOREM IPSUM DOLOR</h3><p>Duis aute irure dolor in repreh enderit in voluptate velit esse cillum</p></div>
  <div class="feature" style="left:613px"><div class="icon ring"><svg width="60" height="60" viewBox="0 0 60 60" fill="none" stroke="#fff" stroke-width="2.5"><circle cx="22" cy="14" r="5"/><circle cx="40" cy="14" r="5"/><path d="M14 48V26h16v22M32 48V26h16v22"/></svg></div><div class="num">03</div><h3>LOREM IPSUM DOLOR</h3><p>Duis aute irure dolor in repreh enderit in voluptate velit esse cillum</p></div>
  <div class="feature" style="left:869px"><div class="icon"><svg width="60" height="60" viewBox="0 0 60 60" fill="none" stroke="#fff" stroke-width="2.5"><circle cx="36" cy="14" r="6"/><path d="M12 46l14-12 10 6 10-14M26 34l-4-10 14-2"/></svg></div><div class="num">04</div><h3>LOREM IPSUM DOLOR</h3><p>Duis aute irure dolor in repreh enderit in voluptate velit esse cillum</p></div>
</section>

<section class="abs about">
  <div role="img" aria-label="Faded photo of a therapist assisting a patient in a rehabilitation room" style="position:absolute;left:300px;top:0;width:700px;height:670px;background:radial-gradient(ellipse at center,rgba(190,196,200,.35),transparent 70%)"></div>
  <div class="about-name">QUILL PHYSICAL<br>THERAPY</div>
  <h2>ABOUT US</h2>
  <p>Lorem ipsum dolor sit amet, consectetur adipiscing elit, sed do eiusmod tempor incididunt ut labore et dolore magna aliqua. Ut enim ad minim veniam, quis nostrud exercitation ullamco laboris nisi ut aliquip ex ea commodo consequat. Duis aute irure dolor in reprehend erit in voluptate velit esse cillum dolore eu fugiat nulla pariatur. Excepteur sint occaecat cupidatat non proident, sunt in culpa qui officia deserunt mollit anim id est laborum.Lorem ipsum dolor sit amet, consectetur adipiscing elit, sed do eiusmod tempor incididunt ut labore et dolore magna aliqua. Ut enim ad minim veniam, quis nostrud exercitation ullamco laboris nisi ut aliquip ex ea commodo consequat. Duis aute irure dolor in reprehenderit in voluptate velit esse cillum dolore eu fugiat nulla pariatur.</p>
  <div class="btn" style="left:612px;top:434px;width:162px;height:44px">LEARN MORE</div>
  <div class="call-label">Call us Today :</div>
  <div class="call-num">+1 555 014 2290</div>
</section>

<section>
  <h2 class="abs heading" style="top:2196px">OUR BRAND &amp; SERVICES</h2>
  <div class="service" style="left:111px"><div class="photo" role="img" aria-label="Therapist treating a patient's shoulder" style="background:linear-gradient(160deg,#c8a894,#7a5d52 60%,#4d3a34)"></div><span>Lorem ipsum dolor</span><div class="go"><svg width="26" height="26" viewBox="0 0 26 26"><circle cx="13" cy="13" r="12" fill="var(--teal)"/><path d="M9 13h8M14 9l4 4-4 4" stroke="#fff" stroke-width="2" fill="none"/></svg></div></div>
  <div class="service" style="left:358px"><div class="photo" role="img" aria-label="Patient raising arm during guided stretch" style="background:linear-gradient(160deg,#e8e4de,#a9a39a 60%,#5f6b6a)"></div><span>Lorem ipsum dolor</span><div class="go"><svg width="26" height="26" viewBox="0 0 26 26"><circle cx="13" cy="13" r="12" fill="var(--teal)"/><path d="M9 13h8M14 9l4 4-4 4" stroke="#fff" stroke-width="2" fill="none"/></svg></div></div>
  <div class="service" style="left:608px"><div class="photo" role="img" aria-label="Patient walking between parallel bars with therapist" style="background:linear-gradient(160deg,#d6dde0,#8fa2a8 60%,#4d5f66)"></div><span>Lorem ipsum dolor</span><div class="go"><svg width="26" height="26" viewBox="0 0 26 26"><circle cx="13" cy="13" r="12" fill="var(--teal)"/><path d="M9 13h8M14 9l4 4-4 4" stroke="#fff" stroke-width="2" fill="none"/></svg></div></div>
  <div class="service" style="left:855px"><div class="photo" role="img" aria-label="Patient exercising on a balance ball" style="background:linear-gradient(160deg,#d9c6b0,#9c8470 60%,#574a44)"></div><span>Lorem ipsum dolor</span><div class="go"><svg width="26" height="26" viewBox="0 0 26 26"><circle cx="13" cy="13" r="12" fill="var(--teal)"/><path d="M9 13h8M14 9l4 4-4 4" stroke="#fff" stroke-width="2" fill="none"/></svg></div></div>
</section>

<section class="abs testi">
  <svg class="abs" style="left:0;top:0" width="1200" height="740" viewBox="0 0 1200 740">
    <defs><linearGradient id="lens" x1="0" y1="0" x2="0" y2="1"><stop offset="0" stop-color="#78c650"/><stop offset=".55" stop-color="#3aa474"/><stop offset="1" stop-color="#138078"/></linearGradient></defs>
    <path d="M0 210 Q600 -40 1200 210 L1200 520 Q600 800 0 520Z" fill="url(#lens)"/>
    <path d="M0 190 Q600 -60 1200 190" fill="none" stroke="var(--teal)" stroke-width="14"/>
    <path d="M300 60 Q800 -10 1200 160" fill="none" stroke="var(--green)" stroke-width="8"/>
    <path d="M0 540 Q600 820 1200 540" fill="none" stroke="var(--teal)" stroke-width="14"/>
    <path d="M0 560 Q500 760 900 700" fill="none" stroke="var(--green)" stroke-width="8"/>
  </svg>
  <h2>WHAT OUR CLIENTS SAY</h2>
  <div class="quote" style="left:111px"><div class="mark">&ldquo;</div><p>Lorem ipsum dolor sit amet, consectetur adipiscing elit, sed do eiusmod tempor incididunt ut labore et dolore magna aliqua. Ut enim ad minim veniam, quis nostrud exercitation ullamco laboris nisi ut aliquip ex ea commodo consequat. Duis aute irure dolor in reprehenderit in voluptate velit esse cillum dolore eu fugiat nulla pariatur.</p><div class="avatar" role="img" aria-label="Client portrait"></div><div class="who">John doe</div><div class="co">Company name</div></div>
  <div class="quote" style="left:615px"><div class="mark">&ldquo;</div><p>Lorem ipsum dolor sit amet, consectetur adipiscing elit, sed do eiusmod tempor incididunt ut labore et dolore magna aliqua. Ut enim ad minim veniam, quis nostrud exercitation ullamco laboris nisi ut aliquip ex ea commodo consequat. Duis aute irure dolor in reprehenderit in voluptate velit esse cillum dolore eu fugiat nulla pariatur.</p><div class="avatar" role="img" aria-label="Client portrait"></div><div class="who">John doe</div><div class="co">Company name</div></div>
  <div class="round" style="left:537px;top:509px"><svg width="12" height="12" viewBox="0 0 12 12"><path d="M8 1L3 6l5 5" stroke="#fff" stroke-width="2" fill="none"/></svg></div>
  <div class="round" style="left:617px;top:509px"><svg width="12" height="12" viewBox="0 0 12 12"><path d="M4 1l5 5-5 5" stroke="#fff" stroke-width="2" fill="none"/></svg></div>
</section>

<section>
  <h2 class="abs heading" style="top:3522px">LATEST BLOG</h2>
  <svg class="abs" style="left:40px;top:3842px" width="34" height="56" viewBox="0 0 34 56"><path d="M30 2L4 28l26 26" stroke="#222" stroke-width="2.5" fill="none"/></svg>
  <svg class="abs" style="left:1128px;top:3842px" width="34" height="56" viewBox="0 0 34 56"><path d="M4 2l26 26L4 54" stroke="#222" stroke-width="2.5" fill="none"/></svg>
  <article class="post" style="left:111px"><div class="photo" role="img" aria-label="Therapist examining a patient's knee" style="background:linear-gradient(150deg,#e6e9ea,#b4bcc0 55%,#6f7f86)"><div class="date">APR<br>05</div></div><h3>LOREM IPSUM DOLOR SIT CONSECTETUR ADI</h3><div class="by">&#9679; BY JOHN DOE</div><p>Lorem ipsum dolor sit amet, consectetur adipiscing elit, sed do eiusmod tempor incididunt ut labore et dolore magna aliqua. Ut enim ad</p><div class="btn">LEARN MORE</div></article>
  <article class="post" style="left:445px"><div class="photo" role="img" aria-label="Therapist stretching a patient's leg on a treatment table" style="background:linear-gradient(150deg,#f0ebe6,#d4b8a4 55%,#e2846a)"><div class="date">FEB<br>11</div></div><h3>LOREM IPSUM DOLOR SIT CONSECTETUR ADI</h3><div class="by">&#9679; BY JOHN DOE</div><p>Lorem ipsum dolor sit amet, consectetur adipiscing elit, sed do eiusmod tempor incididunt ut labore et dolore magna aliqua. Ut enim ad</p><div class="btn">LEARN MORE</div></article>
  <article class="post" style="left:778px"><div class="photo" role="img" aria-label="Patient doing a core exercise with a therapist and an exercise ball" style="background:linear-gradient(150deg,#eceeee,#b9c0c2 55%,#7d8a8e)"><div class="date">DEC<br>28</div></div><h3>LOREM IPSUM DOLOR SIT CONSECTETUR ADI</h3><div class="by">&#9679; BY JOHN DOE</div><p>Lorem ipsum dolor sit amet, consectetur adipiscing elit, sed do eiusmod tempor incididunt ut labore et dolore magna aliqua. Ut enim ad</p><div class="btn">LEARN MORE</div></article>
</section>

<footer class="abs footer">
  <svg class="abs" style="left:0;top:0" width="1200" height="410" viewBox="0 0 1200 410">
    <path d="M0 110 Q500 -20 1200 60 L1200 410 L0 410Z" fill="var(--green)"/>
    <path d="M0 150 Q560 20 1200 100 L1200 410 L0 410Z" fill="var(--teal)"/>
  </svg>
  <div class="fcol" style="left:113px"><h4>QUICK LINKS</h4><ul><li>Home</li><li>About us</li><li>Services</li><li>Reviews</li><li>Contact Us</li></ul></div>
  <div class="fdiv" style="left:300px"></div>
  <div class="fcol" style="left:361px"><h4>INFORMATION</h4><ul><li>Terms &amp; Conditions</li><li>Privacy Policy</li><li>Disclaimer</li><li>Site Map</li><li>Contact Us</li></ul></div>
  <div class="fdiv" style="left:550px"></div>
  <div class="fcol" style="left:624px"><h4>CONTACT INFO</h4><ul>
    <li><svg width="12" height="12" viewBox="0 0 24 24"><path fill="#fff" d="M6.6 10.8a15 15 0 006.6 6.6l2.2-2.2a1 1 0 011-.25 11.4 11.4 0 003.6.57 1 1 0 011 1V20a1 1 0 01-1 1A17 17 0 013 4a1 1 0 011-1h3.5a1 1 0 011 1c0 1.25.2 2.45.57 3.6a1 1 0 01-.25 1z"/></svg>(555) 014-2290</li>
    <li><svg width="12" height="12" viewBox="0 0 12 12"><rect x="1" y="4" width="10" height="6" fill="#fff"/><rect x="3" y="1" width="6" height="3" fill="#fff"/></svg>(555) 014-229</li>
    <li><svg width="12" height="12" viewBox="0 0 14 12"><rect x="1" y="1" width="12" height="10" fill="none" stroke="#fff" stroke-width="1.5"/><path d="M1 1l6 5 6-5" fill="none" stroke="#fff" stroke-width="1.5"/></svg><span style="text-decoration:underline">hello@quillphysio.com</span></li>
    <li style="line-height:16px;align-items:flex-start;margin-top:6px"><svg width="12" height="14" viewBox="0 0 12 16"><path fill="#fff" d="M6 0a6 6 0 016 6c0 4-6 10-6 10S0 10 0 6a6 6 0 016-6zm0 4a2 2 0 100 4 2 2 0 000-4z"/></svg><span>#2868 Lorem ipsum dolor<br>sit amet, consectetur</span></li>
  </ul></div>
  <div class="fdiv" style="left:870px"></div>
  <div class="fcol" style="left:953px"><h4>FOLLOW US</h4><ul style="line-height:34px">
    <li style="line-height:34px"><span class="ic"></span>Community</li>
    <li style="line-height:34px"><span class="ic"></span>Updates</li>
    <li style="line-height:34px"><span class="ic"></span>Reviews</li>
    <li style="line-height:34px"><span class="ic"></span>Careers</li>
  </ul></div>
  <div class="copy">Copyrights &copy; Quill Physical Therapy 2021 | Allrights Reserved</div>
</footer>

</body>
</html>
```